Canadian company needs a packaging design for a new product line of TubGlow Hot Tub & Bath Fragran

We are looking for a packaging design for a new company based in Edmonton, Alberta Canada called TubGlow. We are developing a new product line of liquid and crystal Hot Tub & Bath Fragrances (aromatherapy) for example Lavender will be one of our fragrances. We are looking at the possibilities of using a stand up pouch and or the standard plastic bottles for our fragrance line. There will be different sizes from 150 grams to 600 grams in the crystal and 275 ml in the liquid. We would like to see bright multi-colored designs possibly with picture of the fragrance or a theme like favorite drinks or a more sensual idea. Each one of our fragrances will be a different color the main design needs to be able to have a different color of liquid or crystal in the bottle and possibly parts of the label will change colors for each fragrance. I have attached samples of another brand that we want to improve on.

Target Market(s)

Most of these fragrance are bought by women 70% men 30%
age 25 - 55

Industry/Entity Type

It Company

Requirements
Must have
• bottle size
Fragrance name
Nice to have
• Using the files below I like the circle of colors and possibly it could be made using water drops like in the file and possibly the two "S" could be designed like the third file I just added

Files

```html
<!DOCTYPE html>
<html lang="en">
<head>
<meta charset="utf-8">
<title>TubGlow – Lavender Hot Tub &amp; Bath Aromatherapy</title>
<link rel="stylesheet" href="https://fonts.googleapis.com/css2?family=Poppins:wght@500;600&family=Parisienne&display=swap">
<style>
  :root{
    --purple:#7b2a8a;
    --purple-dark:#6a1f78;
    --purple-light:#9a48a8;
    --gold:#c9a227;
    --panel-top:#ffffff;
    --panel-bottom:#dedede;
    --green:#22a845;
    --green-dark:#137a2c;
    --sand:#d9ccb4;
    --lavender-deep:#55307f;
    --lavender-mid:#7a52a6;
    --stem:#8a9c60;
    --wood:#9c7d58;
    --white:#ffffff;
  }
  *{margin:0;padding:0;box-sizing:border-box}
  html,body{width:1200px;height:722px;overflow:hidden;background:var(--white)}
  .label{position:relative;width:1200px;height:722px;overflow:hidden;font-family:"Poppins",sans-serif}
  .label-art{position:absolute;inset:0}
  .brand-dot{position:absolute;left:664px;top:60px;width:70px;height:70px;border-radius:50%;background:var(--purple-light)}
  .brand{
    position:absolute;left:372px;width:450px;top:128px;
    font-family:"Parisienne",cursive;font-weight:400;color:var(--purple);line-height:0.9;
  }
  .brand-line{display:block}
  .brand-line-top{font-size:86px;padding-left:138px}
  .brand-line-bottom{font-size:118px;padding-left:62px}
  .ribbon{
    position:absolute;height:50px;padding:0 18px;display:flex;align-items:center;justify-content:center;
    background:linear-gradient(180deg,var(--green) 0%,var(--green-dark) 100%);
    color:var(--white);font-weight:500;font-size:28px;white-space:nowrap;
    border:2px solid #e9f5ea;transform-origin:left center;
  }
  .ribbon-top{left:98px;top:590px;width:230px;transform:rotate(-16deg)}
  .ribbon-bottom{left:163px;top:650px;width:258px;transform:rotate(-16deg)}
  .bottle-size{
    position:absolute;left:820px;top:566px;width:242px;text-align:center;
    color:var(--white);font-weight:500;font-size:17px;letter-spacing:1px;
  }
  .fragrance-name{
    position:absolute;left:820px;top:604px;width:242px;text-align:center;
    color:var(--white);font-weight:500;font-size:32px;line-height:1;
  }
  .tagline{
    position:absolute;left:0;right:0;top:672px;text-align:center;
    font-family:"Parisienne",cursive;font-size:34px;line-height:1;color:var(--purple);
  }
</style>
</head>
<body>
<main class="label">
  <svg class="label-art" width="1200" height="722" viewBox="0 0 1200 722">
    <defs>
      <linearGradient id="side-fill" x1="0" y1="0" x2="1" y2="1">
        <stop offset="0" stop-color="#8a349a"/>
        <stop offset="1" stop-color="#7a2a8b"/>
      </linearGradient>
      <linearGradient id="panel-fill" x1="0" y1="0" x2="0" y2="1">
        <stop offset="0" stop-color="var(--panel-top)"/>
        <stop offset="1" stop-color="var(--panel-bottom)"/>
      </linearGradient>
      <linearGradient id="lavender-fill" x1="0.1" y1="0" x2="0.9" y2="1">
        <stop offset="0" stop-color="var(--sand)"/>
        <stop offset="0.3" stop-color="var(--lavender-mid)"/>
        <stop offset="0.6" stop-color="var(--lavender-deep)"/>
        <stop offset="0.82" stop-color="var(--stem)"/>
        <stop offset="1" stop-color="var(--wood)"/>
      </linearGradient>
      <linearGradient id="footer-fill" x1="0" y1="0" x2="0" y2="1">
        <stop offset="0" stop-color="#f2f2f2"/>
        <stop offset="1" stop-color="#ffffff"/>
      </linearGradient>
      <clipPath id="above-footer"><rect x="0" y="0" width="1200" height="655"/></clipPath>
    </defs>

    <rect class="side-panel" x="0" y="0" width="1200" height="655" fill="url(#side-fill)"/>
    <rect class="top-band" x="0" y="0" width="1200" height="32" fill="var(--purple-dark)"/>

    <rect class="centre-panel" x="374" y="32" width="446" height="623" fill="url(#panel-fill)" stroke="var(--gold)" stroke-width="5"/>

    <g clip-path="url(#above-footer)">
      <circle class="photo-ring" cx="600" cy="630" r="340" fill="var(--purple)"/>
      <circle class="photo-window" cx="604" cy="636" r="318" fill="url(#lavender-fill)" role="img" aria-label="Photograph of a bundle of fresh lavender on a wooden surface"/>
      <path class="name-tab" d="M820 655 A121 107 0 0 1 1062 655 Z" fill="var(--purple)"/>
    </g>

    <rect class="footer-band" x="0" y="655" width="1200" height="67" fill="url(#footer-fill)"/>
    <line class="footer-rule" x1="0" y1="656" x2="1200" y2="656" stroke="var(--gold)" stroke-width="4"/>
  </svg>

  <span class="brand-dot" aria-hidden="true"></span>
  <h1 class="brand"><span class="brand-line brand-line-top">Tub</span><span class="brand-line brand-line-bottom">Glow</span></h1>

  <p class="ribbon ribbon-top">Hot Tub &amp; Bath</p>
  <p class="ribbon ribbon-bottom">Aromatherapy</p>

  <p class="bottle-size">275 ml</p>
  <p class="fragrance-name">Lavender</p>
  <p class="tagline">Enhance the Enjoyment</p>
</main>
</body>
</html>
```